International sports company needs packaging design for color box

We need this box for our yoga mats which we will sell online. This mat is very high quality and 100% environmentally friendly. The yoga mat comes in a stylish yoga bag that will be in the box.

Yoga enthusiasts, athletes, gymnasts, actually all people who do sporting activities and value environmental friendliness will be the contact group

The logo should be visible in any case. The creator is free to choose whether to use only the complete logo or the complete logo with the emblem. In terms of style, it should be reminiscent of a packaging box from Corvane's Vextal. Be as timeless, modern and elegant as possible. If an environmentally friendly detail can be added, this would certainly be a plus. Color should be black / white / gray.

Target Market(s)

Germany

Requirements
Must have
• Size for the color box should be 13x13x61.5 cm.

```html
<!DOCTYPE html>
<html lang="en">
<head>
<meta charset="utf-8">
<title>AVERO Yoga Mat – Colour Box Dieline</title>
<link rel="stylesheet" href="https://fonts.googleapis.com/css2?family=Jost:wght@300;400;600&display=swap">
<style>
  :root {
    --backdrop: #d6d6d6;
    --paper: #ffffff;
    --ink: #13120f;
    --fold: #b9b9b9;
    --edge: #9a9a9a;
  }
  html, body {
    margin: 0;
    padding: 0;
    width: 1200px;
    height: 784px;
    overflow: hidden;
    background: var(--backdrop);
  }
  .dieline {
    display: block;
    width: 1200px;
    height: 784px;
  }
  .panel-light { fill: var(--paper); stroke: var(--edge); stroke-width: 0.8; }
  .panel-dark { fill: var(--ink); }
  .fold-line { stroke: var(--fold); stroke-width: 0.8; stroke-dasharray: 4 3; fill: none; }
  .brand-name {
    font-family: "Jost", sans-serif;
    font-weight: 600;
    font-size: 19px;
    letter-spacing: 2px;
    fill: var(--ink);
  }
  .brand-dot { fill: var(--ink); }
  .feature-list {
    font-family: "Jost", sans-serif;
    font-weight: 400;
    font-size: 11.5px;
    letter-spacing: 1.6px;
    fill: var(--ink);
  }
  .product-title {
    font-family: "Jost", sans-serif;
    font-weight: 300;
    font-size: 50px;
    letter-spacing: 7px;
    fill: var(--paper);
  }
  .eco-badge-dark { fill: none; stroke: var(--ink); stroke-width: 1.4; }
  .eco-badge-light { fill: none; stroke: var(--paper); stroke-width: 1.4; }
</style>
</head>
<body>
<svg class="dieline" viewBox="17 40 1120 732" xmlns="http://www.w3.org/2000/svg" aria-label="Flat dieline of the AVERO yoga mat colour box">

  <!-- side panel, top -->
  <g class="side-panel side-panel-top">
    <path class="panel-light" d="M240 78 H925 L1004 88 Q1018 90 1018 104 V212 Q1018 224 1004 226 L925 236 H240 L162 226 Q148 224 148 212 V104 Q148 90 162 88 Z"/>
    <line class="fold-line" x1="240" y1="78" x2="240" y2="236"/>
    <line class="fold-line" x1="925" y1="78" x2="925" y2="236"/>
    <circle class="brand-dot" cx="318" cy="158" r="9"/>
    <text class="brand-name" x="336" y="165">AVERO</text>
    <circle class="eco-badge-dark" cx="557" cy="157" r="36" role="img" aria-label="Eco badge: 100% environmentally friendly yoga mat"/>
    <text class="feature-list">
      <tspan x="668" y="143">HIGH QUALITY YOGA MAT</tspan>
      <tspan x="668" y="165">100% ENVIRONMENTALLY FRIENDLY</tspan>
      <tspan x="668" y="187">COMES IN STYLISH YOGA BAG</tspan>
    </text>
  </g>

  <!-- front panel with end tuck flaps -->
  <g class="front-panel">
    <path class="panel-dark" d="M82 236 H1084 L1104 248 Q1110 252 1110 260 V372 Q1110 380 1104 384 L1084 394 H82 L63 384 Q57 380 57 372 V260 Q57 252 63 248 Z"/>
    <text class="product-title" x="364" y="339">YOGA MAT</text>
    <circle class="eco-badge-light" cx="766" cy="312" r="36" role="img" aria-label="Eco badge: 100% environmentally friendly yoga mat"/>
  </g>

  <!-- side panel, bottom -->
  <g class="side-panel side-panel-bottom">
    <path class="panel-light" d="M240 394 H925 L1004 404 Q1018 406 1018 420 V528 Q1018 540 1004 542 L925 552 H240 L162 542 Q148 540 148 528 V420 Q148 406 162 404 Z"/>
    <line class="fold-line" x1="240" y1="394" x2="240" y2="552"/>
    <line class="fold-line" x1="925" y1="394" x2="925" y2="552"/>
    <circle class="brand-dot" cx="318" cy="478" r="9"/>
    <text class="brand-name" x="336" y="485">AVERO</text>
    <circle class="eco-badge-dark" cx="557" cy="477" r="36" role="img" aria-label="Eco badge: 100% environmentally friendly yoga mat"/>
    <text class="feature-list">
      <tspan x="668" y="463">HIGH QUALITY YOGA MAT</tspan>
      <tspan x="668" y="485">100% ENVIRONMENTALLY FRIENDLY</tspan>
      <tspan x="668" y="507">COMES IN STYLISH YOGA BAG</tspan>
    </text>
  </g>

  <!-- back panel with glue flap -->
  <g class="back-panel">
    <path class="panel-dark" d="M240 552 H925 V710 L915 728 Q910 737 898 737 H267 Q255 737 250 728 L240 710 Z"/>
    <text class="product-title" x="364" y="666">YOGA MAT</text>
    <circle class="eco-badge-light" cx="766" cy="640" r="36" role="img" aria-label="Eco badge: 100% environmentally friendly yoga mat"/>
  </g>
</svg>
</body>
</html>
```